Print materials for 3-star hotel

We are changing up our print materials (notepads, letterheads, key card jackets, small flyer for the room rates) We are a 3 star business hotel in the Philippines and have mainly used grey tones and clean, simple lines. See attached photos for logo and hotel interior photos.

Target Market(s)

Business

Contact Information for Business Card

Corvale Terrace Hotel
Lindwell Banca Avenue corner Tolenta St Cebu City 6000 Philippines
Tel: +63 32 481 7302
Mobile: +63 917 648 2095
www.corvaleterracehotel.example

Font styles to use
Serif
Sans Serif

Requirements
Must have
• Simple
• Readable font and font size
Nice to have
• Neutral colors, grey and taupes
Should not have
• No purples and bright blues

```html
<!DOCTYPE html>
<html lang="en">
<head>
<meta charset="utf-8">
<title>Corvale Terrace Hotel — Business Card</title>
<link rel="stylesheet" href="https://fonts.googleapis.com/css2?family=Cinzel:wght@400&family=Roboto+Condensed:wght@700&family=Roboto:wght@400;500&display=swap">
<style>
  :root {
    --backdrop: #2b2b2d;
    --card: #1d1d1e;
    --ink: #f4f4f4;
    --ink-soft: #d9d9d9;
    --rule: #6a6a6a;
  }
  * { box-sizing: border-box; margin: 0; padding: 0; }
  html, body {
    width: 1200px; height: 900px; overflow: hidden;
    background: var(--backdrop);
  }
  .canvas {
    position: relative; width: 1200px; height: 900px;
    display: flex; flex-direction: column; align-items: center; justify-content: center; gap: 44px;
  }
  .card {
    position: relative; width: 640px; height: 360px;
    background: var(--card); color: var(--ink);
    box-shadow: 0 14px 30px rgba(0,0,0,.45);
  }
  /* Front */
  .card--front {
    display: flex; flex-direction: column; align-items: center; justify-content: center;
  }
  .brand { display: flex; flex-direction: column; align-items: center; gap: 14px; }
  .brand__square { width: 46px; height: 46px; background: var(--ink); }
  .brand__name {
    font-family: "Cinzel", serif; font-weight: 400;
    font-size: 26px; letter-spacing: 4px; text-align: center; line-height: 1.15;
    color: var(--ink);
  }
  .front__web {
    margin-top: 44px;
    font-family: "Roboto", sans-serif; font-size: 14px; letter-spacing: 6px;
    color: var(--ink-soft);
  }
  /* Back */
  .card--back { padding: 0; }
  .person {
    position: absolute; right: 382px; top: 92px; text-align: right;
  }
  .person__name {
    font-family: "Roboto Condensed", sans-serif; font-weight: 700;
    font-size: 38px; letter-spacing: .5px; line-height: 1;
  }
  .person__title {
    margin-top: 6px;
    font-family: "Roboto", sans-serif; font-weight: 500; font-size: 15px; letter-spacing: .5px;
  }
  .divider {
    position: absolute; left: 284px; top: 70px; width: 1px; height: 132px;
    background: linear-gradient(to bottom, transparent, var(--rule) 20%, var(--rule) 80%, transparent);
  }
  .contacts {
    position: absolute; left: 310px; top: 74px; list-style: none;
    font-family: "Roboto", sans-serif; font-size: 16px; line-height: 25px;
  }
  .contacts li { display: flex; align-items: center; gap: 10px; }
  .icon { width: 14px; height: 14px; fill: var(--ink); flex: none; }
  .address {
    position: absolute; left: 40px; bottom: 44px;
    display: flex; align-items: center; gap: 8px;
    font-family: "Roboto", sans-serif; font-size: 16px;
  }
</style>
</head>
<body>
<main class="canvas">
  <section class="card card--front" aria-label="Card front">
    <div class="brand">
      <span class="brand__square" aria-hidden="true"></span>
      <h1 class="brand__name">Corvale Terrace<br>Hotel</h1>
    </div>
    <p class="front__web">www.corvaleterracehotel.example</p>
  </section>

  <section class="card card--back" aria-label="Card back">
    <div class="person">
      <h2 class="person__name">ELENA MARSH</h2>
      <p class="person__title">CEO/FOUNDER</p>
    </div>
    <span class="divider" aria-hidden="true"></span>
    <ul class="contacts">
      <li><svg class="icon" viewBox="0 0 16 16" aria-hidden="true"><path d="M3.5 1l2.5 3-1.5 2c1 2 2.5 3.5 4.5 4.5l2-1.5 3 2.5-1.5 2.5C7 14 2 9 1 2.5z"/></svg>+63 32 481 7302</li>
      <li><svg class="icon" viewBox="0 0 16 16" aria-hidden="true"><path d="M4 0h8v16H4zM5.5 2v10h5V2zM7 13.2h2v1.4H7z" fill-rule="evenodd"/></svg>+63 917 648 2095</li>
      <li><svg class="icon" viewBox="0 0 16 16" aria-hidden="true"><path d="M4 1h8v4H4zM1 6h14v7h-3v2H4v-2H1zM5 10v4h6v-4z" fill-rule="evenodd"/></svg>+63 32 481 7315</li>
      <li><svg class="icon" viewBox="0 0 16 16" aria-hidden="true"><path d="M1 3h14v10H1zM2 4.5v.4l6 4 6-4v-.4z" fill-rule="evenodd"/></svg>stay@corvaleterrace.example</li>
      <li><svg class="icon" viewBox="0 0 16 16" aria-hidden="true"><circle cx="8" cy="8" r="7"/><path d="M8 1v14M1 8h14" stroke="#1d1d1e" stroke-width="1.2" fill="none"/></svg>www.corvaleterracehotel.example</li>
    </ul>
    <p class="address"><svg class="icon" viewBox="0 0 16 16" aria-hidden="true"><path d="M8 0a5.5 5.5 0 0 1 5.5 5.5C13.5 10 8 16 8 16S2.5 10 2.5 5.5A5.5 5.5 0 0 1 8 0zm0 3.3a2.2 2.2 0 1 0 0 4.4 2.2 2.2 0 0 0 0-4.4z" fill-rule="evenodd"/></svg>Lindwell Banca Avenue corner Tolenta St, Cebu City 6000</p>
  </section>
</main>
</body>
</html>
```